Stationery Design Project for Marketing Consultancy

I have started a new consultancy business and require the following elements to be designed using existing logo:
• Business card
• Letterhead
• Envelope (DL, C4, C5)
• Microsoft word template for report writing
• A4 Presentation Folder
• Powerpoint template
COPY FOR FRONT AND BACK OF BUSINESS CARD
logo
'Clear Thinking. Steady Growth Ahead' slogan (but no need to use existing lockup with logo)
name, B Bus. Mktg, Grad Dip Digital Mktg, CPM (post nominal abbreviations in smaller font)
mobile: 04XX-XXX-XXX (I will give details to the winner to add)
website: www.tolvarin.com.au
email: info@tolvarin.com.au
COPY FOR LETTERHEAD
Logo
Company Name
Please, submit your designs that include business card, letterhead and envelope. Once selected the winner will be asked to complete the project by creating the rest of the artwork.
FINAL FILES
Print ready files to be supplied as well as Indesign files so that minor amends can be made if necessary in future.
• Layered vectors in EPS & PDF
• Screen quality JPEG & PNGs
ABOUT THE BUSINESS: TOLVARIN
I work with clients to understand their business challenges, developing and executing measurable marketing strategies tied to key business metrics. Services include:
Services include:
• Business planning and business development
• Marketing and brand strategy
• Insight-driven integrated campaigns
• Loyalty programs and retention marketing
• Marketing automation
• Direct marketing (traditional and digital)
• Content strategy and development
Hi everyone,
Target Market(s)
Corporate decision makers (heads of marketing, general managers etc) and small to medium sized business owners. Predominately male aged 35+
Industry/Entity Type
Marketing
Requirements
Must have
- BRAND PERSONALITY
The successful design will communicate brand personality. I am a professional, results-driven entrepreneur, but want to show off my creative flair.
MEMORABILITY
Looking for a unique and eye-catching design. Am considering special printing effects (die cuts, letterpress, interactive elements, embossing, foiling etc) or a striking minimalist approach.
Nice to have
- I have a mission that could be incorporated on reverse if room -
Turning insights into actions & passion into profit.
Should not have
- Use of pink or green.

```html
<!DOCTYPE html>
<html lang="en">
<head>
<meta charset="utf-8">
<title>Tolvarin – Business Card</title>
<link rel="stylesheet" href="https://fonts.googleapis.com/css2?family=Arimo:wght@400;700&display=swap">
<style>
  :root {
    --backdrop: #2b2b2b;
    --card-white: #ffffff;
    --card-white-shade: #e9e9e9;
    --card-dark: #4a4a4a;
    --card-dark-text: #3f3f3f;
    --accent-orange: #f0821e;
    --ink: #4d4d4d;
    --ink-strong: #2a2a2a;
  }
  * { box-sizing: border-box; margin: 0; padding: 0; }
  html, body {
    width: 1200px; height: 900px; overflow: hidden;
    background: var(--backdrop);
    font-family: "Arimo", Arial, sans-serif;
  }
  .stage {
    position: relative; width: 1200px; height: 900px;
    display: flex; align-items: center; justify-content: center; gap: 40px;
  }
  .card {
    position: relative; width: 540px; height: 309px; overflow: hidden;
  }
  .card-front {
    background: linear-gradient(160deg, var(--card-white) 40%, var(--card-white-shade) 100%);
    color: var(--ink);
  }
  .holder-name {
    position: absolute; left: 44px; top: 48px;
    font-size: 24px; color: var(--accent-orange); font-weight: 400;
  }
  .holder-credentials {
    position: absolute; left: 44px; top: 80px;
    font-size: 13px; color: var(--ink);
  }
  .contact-list {
    position: absolute; left: 44px; top: 152px; list-style: none;
    font-size: 14px; line-height: 22px; color: var(--ink);
  }
  .contact-list li { display: flex; align-items: center; gap: 10px; }
  .contact-list svg { width: 12px; height: 12px; flex: none; }
  .brand-lockup {
    position: absolute; right: 36px; bottom: 34px; text-align: left;
  }
  .brand-name {
    font-size: 26px; font-weight: 700; color: var(--ink-strong); letter-spacing: 1px;
  }
  .brand-tagline {
    font-size: 8px; font-weight: 700; color: var(--ink-strong);
    letter-spacing: 0.6px; text-transform: uppercase; margin-top: 3px;
    white-space: nowrap;
  }
  .card-back {
    background: var(--card-dark);
    display: flex; align-items: center; justify-content: center;
  }
  .back-brand {
    font-size: 64px; font-weight: 700; color: var(--card-dark-text); letter-spacing: 3px;
  }
</style>
</head>
<body>
<main class="stage">
  <section class="card card-front" aria-label="Business card front">
    <h1 class="holder-name">Nadia Fenwick</h1>
    <p class="holder-credentials">B Bus. Mktg, Grad Dip Digital Mktg, CPM</p>
    <ul class="contact-list">
      <li>
        <svg viewBox="0 0 12 12" aria-hidden="true"><rect x="3" y="0.5" width="6" height="11" rx="1" fill="var(--accent-orange)"/><rect x="4" y="2" width="4" height="6" fill="#fff"/></svg>
        04XX-XXX-XXX
      </li>
      <li>
        <svg viewBox="0 0 12 12" aria-hidden="true"><rect x="0.5" y="2" width="11" height="8" rx="1" fill="var(--accent-orange)"/><path d="M1 2.5 L6 6.5 L11 2.5" stroke="#fff" stroke-width="1" fill="none"/></svg>
        info@tolvarin.com.au
      </li>
      <li>
        <svg viewBox="0 0 12 12" aria-hidden="true"><circle cx="6" cy="6" r="5.5" fill="var(--accent-orange)"/><ellipse cx="6" cy="6" rx="2.2" ry="5" stroke="#fff" stroke-width="0.9" fill="none"/><line x1="1" y1="6" x2="11" y2="6" stroke="#fff" stroke-width="0.9"/></svg>
        www.tolvarin.com.au
      </li>
    </ul>
    <div class="brand-lockup">
      <div class="brand-name">TOLVARIN</div>
      <div class="brand-tagline">Clear Thinking. Steady Growth Ahead</div>
    </div>
  </section>
  <section class="card card-back" aria-label="Business card back">
    <div class="back-brand">TOLVARIN</div>
  </section>
</main>
</body>
</html>
```